Blue Heron Journeys

We are a predominantly online travel agency with high-end (first/business class) clients. I'm looking to either have our existing logo revamped or a new logo created with business card layout. I prefer to work with existing logo if possible so it remains familiar with existing clientele. I have uploaded a yellow business card layout showing icons on one side of the card. I would like to keep my existing colours, not yellow. could the company name/tag line go over the icons?
Industry/Entity Type
Business
Contact Information for Business Card
Lucinda Fairley
Director
(I.A.T.A. 07715463)
(Corvano Pty. Ltd) ABN 61 574 203 918
512/18 Kendrick Lane
Wattle Reach | NSW 2577 | Australia
www.blueheronjourneys.com.au
m: + 61 (0) 417 588 130
t: + 61 (0) 2 9416 2058
e: lucinda@blueheronjourneys.com.au

```html
<!DOCTYPE html>
<html lang="en">
<head>
<meta charset="utf-8">
<title>Blue Heron Journeys – Business Card</title>
<link href="https://fonts.googleapis.com/css2?family=Didact+Gothic&family=Source+Sans+3:wght@400;600;700&display=swap" rel="stylesheet">
<style>
  :root {
    --page: #2b2c30;
    --card: #ffffff;
    --ink: #111111;
    --ink-soft: #333333;
    --rule: #9a9a9a;
    --rule-light: #c8c8c8;
  }
  * { box-sizing: border-box; margin: 0; padding: 0; }
  html, body {
    width: 1200px; height: 864px; overflow: hidden;
    background: var(--page);
  }
  body { position: relative; font-family: "Source Sans 3", "Helvetica Neue", Arial, sans-serif; color: var(--ink); }

  .card {
    position: absolute;
    width: 560px; height: 320px;
    background: var(--card);
  }
  .card--front { left: 230px; top: 70px; }
  .card--back  { left: 410px; top: 470px; }

  .brand {
    position: absolute; left: 0; right: 0;
    display: flex; flex-direction: column; align-items: center;
  }
  .card--front .brand { top: 92px; }
  .card--back .brand { top: 40px; }

  .brand__name {
    font-family: "Source Sans 3", "Helvetica Neue", Arial, sans-serif;
    font-weight: 400;
    font-size: 44px;
    letter-spacing: 0.5px;
    color: var(--ink);
    line-height: 1;
  }
  .brand__rule {
    width: 330px; height: 1px;
    background: var(--rule);
    margin-top: 14px;
  }
  .brand__tagline {
    font-family: "Didact Gothic", "Century Gothic", sans-serif;
    font-size: 21px;
    letter-spacing: 1.5px;
    color: var(--ink-soft);
    margin-top: 6px;
  }

  .card__divider {
    position: absolute; left: 22px; right: 22px; top: 168px;
    height: 1px; background: var(--rule-light);
  }

  .person {
    position: absolute; left: 22px; top: 180px;
    font-size: 15px; line-height: 18px; color: var(--ink-soft);
  }
  .person__name {
    font-weight: 700; font-size: 19px; line-height: 22px;
    color: var(--ink); letter-spacing: 0.3px;
  }

  .contact {
    position: absolute; right: 22px; bottom: 22px;
    list-style: none;
    font-size: 15px; line-height: 21px; color: var(--ink);
    text-align: right;
  }
  .contact__item { display: flex; align-items: center; justify-content: flex-end; gap: 8px; }
  .contact__icon { width: 12px; height: 12px; flex: none; }
</style>
</head>
<body>

  <section class="card card--front" aria-label="Business card front">
    <div class="brand">
      <span class="brand__name">Blue Heron Journeys</span>
      <span class="brand__rule"></span>
      <span class="brand__tagline">chart your own course</span>
    </div>
  </section>

  <section class="card card--back" aria-label="Business card back">
    <div class="brand">
      <span class="brand__name">Blue Heron Journeys</span>
      <span class="brand__rule"></span>
      <span class="brand__tagline">chart your own course</span>
    </div>

    <div class="card__divider"></div>

    <div class="person">
      <p class="person__name">LUCINDA FAIRLEY</p>
      <p>Director</p>
      <p>512/18 Kendrick Lane,</p>
      <p>Wattle Reach NSW 2577,</p>
      <p>Australia</p>
    </div>

    <ul class="contact">
      <li class="contact__item">+ 61 (0) 417 588 130
        <svg class="contact__icon" viewBox="0 0 24 24" aria-hidden="true"><path fill="#111" d="M6.6 10.8a15.1 15.1 0 0 0 6.6 6.6l2.2-2.2c.3-.3.7-.4 1-.2 1.1.4 2.3.6 3.6.6.6 0 1 .4 1 1V20c0 .6-.4 1-1 1A17 17 0 0 1 3 4c0-.6.4-1 1-1h3.5c.6 0 1 .4 1 1 0 1.3.2 2.5.6 3.6.1.3 0 .7-.2 1z"/></svg>
      </li>
      <li class="contact__item">lucinda@blueheronjourneys.com.au
        <svg class="contact__icon" viewBox="0 0 24 24" aria-hidden="true"><rect x="2" y="5" width="20" height="14" fill="#111"/><path d="M2 5l10 8 10-8" fill="none" stroke="#fff" stroke-width="1.6"/></svg>
      </li>
      <li class="contact__item">www.blueheronjourneys.com.au
        <svg class="contact__icon" viewBox="0 0 24 24" aria-hidden="true"><circle cx="12" cy="12" r="11" fill="#111"/><ellipse cx="12" cy="12" rx="4.5" ry="10" fill="none" stroke="#fff" stroke-width="1.4"/><path d="M2 12h20" stroke="#fff" stroke-width="1.4"/></svg>
      </li>
    </ul>
  </section>

</body>
</html>
```